Retail Jewelry Business Card Design Project

We are in need of a new business card design for a retail jewelry store. This store is in the business of fine jewelry including but not specific to bridal jewelry, diamonds, designer jewelry and watches.

This store has been in business for 20 years but continues to strive for a modern professional appeal. The main colors use for this business are a royal blue, white and silver.

Target Market(s)

Target market is ages 18-50

Industry/Entity Type

Jewelry

Requirements
Must have
• Sales Person Name
Sales Person Email Address

Store Address
Store Phone
Website

Standard business card size. No odd shapes or sizes.
Nice to have
• Overall modern feel for card.

We have thought that a design with a nice feature of the logo on the back of the card would be nice but open to ideas.
Should not have
• No specific images of jewelry should be used.

```html
<!DOCTYPE html>
<html lang="en">
<head>
<meta charset="utf-8">
<title>Marlow Reed Fine Jewelry – Business Cards</title>
<link rel="stylesheet" href="https://fonts.googleapis.com/css2?family=Source+Sans+3:wght@400;600&display=swap">
<style>
  :root {
    --stage: #7a5a40;
    --label: #1c1410;
    --paper: #ffffff;
    --royal: #2b3192;
    --lavender: #7470b4;
    --ink-blue: #35389a;
    --ink-dark: #2a2a2a;
    --on-dark: #ffffff;
    --font: "Source Sans 3", "Myriad Pro", Arial, sans-serif;
  }
  * { box-sizing: border-box; margin: 0; padding: 0; }
  html, body { width: 1200px; height: 788px; overflow: hidden; }
  body {
    position: relative;
    background: var(--stage);
    font-family: var(--font);
  }
  .side-label {
    position: absolute;
    width: 525px;
    text-align: center;
    font-size: 22px;
    font-weight: 400;
    color: var(--label);
  }
  .card {
    position: absolute;
    width: 525px;
    height: 300px;
    border-radius: 22px;
    overflow: hidden;
  }
  .card--white { background: var(--paper); }
  .card--royal { background: var(--royal); }
  .card--lavender { background: var(--lavender); }

  .front-accent {
    position: absolute;
    left: 0; top: 135px;
    width: 6px; height: 137px;
    background: var(--royal);
  }
  .front-brand {
    position: absolute;
    left: 25px; top: 34px;
    font-weight: 600;
    color: var(--ink-blue);
    line-height: 1;
  }
  .front-brand .brand-name { display: block; font-size: 38px; }
  .front-brand .brand-line { display: block; font-size: 17px; letter-spacing: 2px; margin-top: 8px; text-transform: uppercase; }

  .person-name {
    position: absolute;
    left: 25px; top: 135px;
    font-size: 17px;
    color: var(--ink-blue);
  }
  .contact-list {
    position: absolute;
    left: 25px; top: 182px;
    list-style: none;
  }
  .contact-list li {
    display: flex;
    align-items: center;
    height: 24px;
    font-size: 13px;
    color: var(--ink-dark);
  }
  .contact-list svg { width: 11px; height: 11px; margin-right: 7px; flex: none; }

  .back-brand {
    position: absolute;
    left: 0; right: 0; top: 78px;
    text-align: center;
    font-weight: 600;
    line-height: 1;
  }
  .back-brand .brand-name { display: block; font-size: 56px; }
  .back-brand .brand-line { display: block; font-size: 21px; letter-spacing: 3px; margin-top: 12px; text-transform: uppercase; }
  .back-url {
    position: absolute;
    left: 0; right: 0; bottom: 24px;
    text-align: center;
    font-size: 13.5px;
    letter-spacing: 2px;
  }
  .card--white .back-brand, .card--white .back-url { color: var(--ink-blue); }
  .card--royal .back-brand, .card--royal .back-url { color: var(--on-dark); }
  .card--lavender .back-brand { color: var(--royal); }
  .card--lavender .back-url { color: var(--ink-dark); }
</style>
</head>
<body>
  <div class="side-label" style="left:55px; top:33px;">Front</div>
  <div class="side-label" style="left:622px; top:33px;">Back - 1</div>
  <div class="side-label" style="left:55px; top:403px;">Back - 2</div>
  <div class="side-label" style="left:622px; top:403px;">Back - 3</div>

  <section class="card card--white" style="left:55px; top:73px;">
    <div class="front-brand">
      <span class="brand-name">Marlow Reed</span>
      <span class="brand-line">Fine Jewelry</span>
    </div>
    <div class="front-accent"></div>
    <p class="person-name">Marlow Reed Ainsley</p>
    <ul class="contact-list">
      <li>
        <svg viewBox="0 0 12 12"><circle cx="6" cy="6" r="5.2" fill="none" stroke="#333" stroke-width="1"/><path d="M4 3.2 L5 3 L5.6 4.6 L4.9 5.1 Q5.6 6.6 6.9 7.1 L7.4 6.4 L9 7 L8.8 8 Q6 8.6 3.6 5 Z" fill="#333"/></svg>
        555-284-0193
      </li>
      <li>
        <svg viewBox="0 0 12 12"><path d="M1 4.5 L6 1.5 L11 4.5 V10.5 H1 Z" fill="#333"/><path d="M1.8 4.8 L6 7.5 L10.2 4.8" fill="none" stroke="#fff" stroke-width="1"/></svg>
        marlow@marlowreedjewelry.com
      </li>
      <li>
        <svg viewBox="0 0 12 12" fill="none" stroke="#333" stroke-width="0.9"><circle cx="6" cy="6" r="5"/><ellipse cx="6" cy="6" rx="2.2" ry="5"/><path d="M1 6 H11 M2 3.3 H10 M2 8.7 H10"/></svg>
        www.marlowreedjewelry.com
      </li>
      <li>
        <svg viewBox="0 0 12 12"><path d="M6 1 L11.5 6 H9.8 V11 H7.2 V8 H4.8 V11 H2.2 V6 H0.5 Z" fill="#333"/></svg>
        820 Linden Avenue, Bay Harbor, FL 32400
      </li>
    </ul>
  </section>

  <section class="card card--white" style="left:622px; top:73px; width:523px;">
    <div class="back-brand">
      <span class="brand-name">Marlow Reed</span>
      <span class="brand-line">Fine Jewelry</span>
    </div>
    <p class="back-url">www.marlowreedjewelry.com</p>
  </section>

  <section class="card card--royal" style="left:55px; top:446px; height:299px;">
    <div class="back-brand">
      <span class="brand-name">Marlow Reed</span>
      <span class="brand-line">Fine Jewelry</span>
    </div>
    <p class="back-url">www.marlowreedjewelry.com</p>
  </section>

  <section class="card card--lavender" style="left:622px; top:446px; width:523px; height:299px;">
    <div class="back-brand">
      <span class="brand-name">Marlow Reed</span>
      <span class="brand-line">Fine Jewelry</span>
    </div>
    <p class="back-url">www.marlowreedjewelry.com</p>
  </section>
</body>
</html>
```